Flooring Billboard Highlighting Large In Stock Inventory

Looking to create a billboard that primarily highlights our logo but also calls out our large in stock inventory and has the city we are located in and phone number at the bottom. Looking for a professional looking design, that is simplistic yet informative.

Location: Marlow, WI, Near Exit 114

Phone: (715) 638-9047

Website: www.tilecrestwi.com

Products: Carpet, Hardwood, Laminate, Vinyl, Luxury Vinyl Plank & Window Treatments

Callouts:
-Free Estimates
-Wisconsin's In Stock Flooring Store
-Slogan: "Big city selection, small town service"

Target Market(s)

Home buyers, DIY'ers, Remoderls, designers

Industry/Entity Type

Flooring, Construction

Font styles to use
Serif

Requirements
Must have
• My logo, location, phone number and call out our large in stock inventory
Nice to have
• Call out the products we have and our slogan

```html
<!DOCTYPE html>
<html lang="en">
<head>
<meta charset="utf-8">
<title>Tilecrest Billboard</title>
<link href="https://fonts.googleapis.com/css2?family=Signika:wght@600;700&family=Oswald:wght@500&display=swap" rel="stylesheet">
<style>
  :root {
    --teal: #268a93;
    --rust: #b2530d;
    --white: #ffffff;
    --ink: #111111;
    --backdrop: #ebe8e8;
  }
  html, body {
    margin: 0;
    width: 1200px;
    height: 1192px;
    overflow: hidden;
    background: var(--backdrop);
  }
  .billboard {
    position: absolute;
    left: 20px;
    top: 413px;
    width: 1160px;
    height: 366px;
    font-family: "Signika", sans-serif;
  }
  .billboard-shapes {
    position: absolute;
    inset: 0;
  }
  .brand-name {
    position: absolute;
    left: 40px;
    top: 78px;
    margin: 0;
    font-family: "Signika", sans-serif;
    font-weight: 700;
    font-size: 118px;
    line-height: 1;
    color: var(--teal);
    letter-spacing: -1px;
  }
  .slogan {
    position: absolute;
    left: 570px;
    top: 12px;
    width: 580px;
    margin: 0;
    text-align: center;
    color: var(--white);
    font-weight: 700;
    font-size: 46px;
    line-height: 58px;
    text-transform: uppercase;
  }
  .product {
    position: absolute;
    height: 31px;
    background: var(--rust);
    color: var(--white);
    font-weight: 700;
    font-size: 23px;
    line-height: 31px;
    text-align: center;
  }
  .callouts-bar {
    position: absolute;
    left: 551px;
    top: 222px;
    width: 571px;
    height: 31px;
    background: var(--teal);
    color: var(--white);
    font-weight: 700;
    font-size: 23px;
    line-height: 31px;
    text-align: center;
  }
  .callouts-list {
    position: absolute;
    left: 548px;
    top: 258px;
    margin: 0;
    color: var(--ink);
    font-weight: 700;
    font-size: 21px;
    line-height: 28px;
    white-space: nowrap;
  }
  .contact {
    position: absolute;
    display: flex;
    align-items: center;
    gap: 10px;
    color: var(--white);
    font-family: "Oswald", sans-serif;
    font-weight: 500;
    font-size: 31px;
    line-height: 1;
    white-space: nowrap;
  }
  .contact svg { flex: none; }
</style>
</head>
<body>
  <div class="billboard">
    <svg class="billboard-shapes" viewBox="0 0 1160 366" width="1160" height="366">
      <rect width="1160" height="366" fill="var(--white)"/>
      <polygon points="490,0 505,0 563,134 548,134" fill="var(--rust)"/>
      <polygon points="505,0 1160,0 1160,132 563,132" fill="var(--teal)"/>
      <polygon points="0,292 675,292 722,366 0,366" fill="var(--teal)"/>
      <polygon points="695,307 1160,307 1160,366 733,366" fill="var(--rust)"/>
    </svg>

    <p class="brand-name">Tilecrest</p>

    <h1 class="slogan">Big City Selection,<br>Small Town Service</h1>

    <div class="product" style="left:562px;top:143px;width:113px">Carpet</div>
    <div class="product" style="left:685px;top:143px;width:157px">Hardwood</div>
    <div class="product" style="left:847px;top:143px;width:141px">Laminate</div>
    <div class="product" style="left:997px;top:141px;width:141px">Vinyl</div>
    <div class="product" style="left:562px;top:182px;width:113px">Luxury</div>
    <div class="product" style="left:684px;top:182px;width:141px">Vinyl Plank</div>
    <div class="product" style="left:847px;top:182px;width:291px">Window Treatments</div>

    <div class="callouts-bar">Callouts</div>
    <p class="callouts-list">• Free Estimates &nbsp;• Wisconsin's In Stock Flooring Store</p>

    <div class="contact" style="left:26px;top:311px">
      <svg width="36" height="36" viewBox="0 0 24 24" fill="none" stroke="currentColor" stroke-width="2" stroke-linecap="round" stroke-linejoin="round">
        <path d="M5 3h3l2 5-2.5 1.5a11 11 0 0 0 7 7L16 14l5 2v3a2 2 0 0 1-2 2A17 17 0 0 1 3 5a2 2 0 0 1 2-2z"/>
        <path d="M15 3a6 6 0 0 1 6 6M15 7a2 2 0 0 1 2 2"/>
      </svg>
      <span>(715) 638-9047</span>
    </div>
    <div class="contact" style="left:312px;top:311px">
      <svg width="38" height="38" viewBox="0 0 24 24" fill="none" stroke="currentColor" stroke-width="2">
        <circle cx="12" cy="12" r="10"/>
        <ellipse cx="12" cy="12" rx="4" ry="10"/>
        <path d="M2 12h20"/>
      </svg>
      <span>www.tilecrestwi.com</span>
    </div>
    <div class="contact" style="left:786px;top:321px">
      <svg width="24" height="32" viewBox="0 0 24 32" fill="currentColor">
        <path d="M12 0a11 11 0 0 0-11 11c0 8 11 21 11 21s11-13 11-21A11 11 0 0 0 12 0zm0 15a4 4 0 1 1 0-8 4 4 0 0 1 0 8z"/>
      </svg>
      <span>Marlow, WI, Near Exit 114</span>
    </div>
  </div>
</body>
</html>
```